Copper Lantern

Need a business card for our restaurant. Restaurant and Bar in the mountains of North Idaho. Rustic looking card

rustic design, wood and metal looking, primarily neutral colors

• Name, address, phone number, website, email address

```html
<!DOCTYPE html>
<html lang="en">
<head>
<meta charset="utf-8">
<title>Copper Lantern – Business Card</title>
<link href="https://fonts.googleapis.com/css2?family=Lato:wght@400;700&display=swap" rel="stylesheet">
<style>
  :root {
    --bg: #2b2b2b;
    --card: #1c1c1c;
    --card-edge: #141414;
    --pattern-dark: #151515;
    --pattern-light: #3a3a3a;
    --ink: #ffffff;
    --ink-soft: #e6e6e6;
    --rule: #8a8a8a;
  }
  * { box-sizing: border-box; margin: 0; padding: 0; }
  html, body { width: 1200px; height: 694px; overflow: hidden; }
  body {
    background: var(--bg);
    font-family: "Lato", Arial, sans-serif;
    color: var(--ink);
    display: flex;
    align-items: center;
    justify-content: center;
    gap: 40px;
  }
  .card {
    width: 540px;
    height: 309px;
    border-radius: 22px;
    background: var(--card);
    box-shadow: 0 14px 30px rgba(0,0,0,.45);
    position: relative;
    overflow: hidden;
  }
  /* Front */
  .card-front .pattern-field {
    position: absolute; inset: 0;
    background: radial-gradient(ellipse at 70% 30%, var(--pattern-light), var(--pattern-dark) 70%);
  }
  .card-front .front-name {
    position: absolute; left: 0; right: 0; top: 50%;
    transform: translateY(-50%);
    text-align: center;
    font-weight: 700;
    font-size: 22px;
    letter-spacing: 1px;
    color: var(--ink);
  }
  /* Back */
  .card-back { display: flex; }
  .brand-side {
    width: 55%;
    display: flex; align-items: center; justify-content: center;
    gap: 12px;
  }
  .brand-dot {
    width: 18px; height: 18px; border-radius: 50%;
    background: var(--ink);
  }
  .brand-name {
    font-weight: 700; font-size: 22px; color: var(--ink);
  }
  .divider {
    width: 1px; margin: 44px 0;
    background: linear-gradient(var(--card), var(--rule), var(--card));
  }
  .contact-side {
    padding: 48px 0 0 26px;
    flex: 1;
  }
  .person-name { font-weight: 700; font-size: 22px; }
  .person-role { font-size: 14px; color: var(--ink-soft); margin-top: 4px; }
  .address { font-size: 14px; line-height: 1.35; margin-top: 18px; color: var(--ink-soft); }
  .contact-list { list-style: none; margin-top: 18px; font-size: 14px; color: var(--ink-soft); }
  .contact-list li { display: flex; align-items: center; gap: 9px; margin-bottom: 7px; }
  .contact-list svg { width: 14px; height: 14px; flex: none; }
</style>
</head>
<body>
  <section class="card card-front">
    <div class="pattern-field" role="img" aria-label="Embossed repeating pattern of the restaurant emblem on black"></div>
    <div class="front-name">Copper Lantern</div>
  </section>

  <section class="card card-back">
    <div class="brand-side">
      <span class="brand-dot"></span>
      <span class="brand-name">Copper Lantern</span>
    </div>
    <div class="divider"></div>
    <div class="contact-side">
      <h1 class="person-name">Daniel Hayes</h1>
      <p class="person-role">Owner</p>
      <p class="address">421, Address line goes here<br>45452, Country name</p>
      <ul class="contact-list">
        <li>
          <svg viewBox="0 0 16 16"><path fill="#fff" d="M3.6 1.5l2.2 2.6-1.3 1.6c.9 2 2.4 3.5 4.4 4.4l1.6-1.3 2.6 2.2-1.3 2.1C7 13 3 9 1.5 4.1z"/></svg>
          123.456.7890
        </li>
        <li>
          <svg viewBox="0 0 16 16"><rect x="1" y="3" width="14" height="10" fill="#fff"/><path d="M1 3l7 6 7-6" fill="none" stroke="#1c1c1c" stroke-width="1.3"/></svg>
          info@webname.com
        </li>
        <li>
          <svg viewBox="0 0 16 16"><circle cx="8" cy="8" r="7" fill="#fff"/><path d="M1 8h14M8 1c-3 3-3 11 0 14M8 1c3 3 3 11 0 14" fill="none" stroke="#1c1c1c" stroke-width="1"/></svg>
          www.website.com
        </li>
      </ul>
    </div>
  </section>
</body>
</html>
```